Maple Gable Business Card

Colors can be blue, grey and white as you see in the attached logo. Needs to have a spot for name, title, phone, email, address, and website. There also needs to be a spot for an agent's picture.

Contact Information for Business Card

See project description.

Colors

Designer to choose colors to be used in the design.

```html
<!DOCTYPE html>
<html lang="en">
<head>
<meta charset="utf-8">
<title>Maple Gable Business Card</title>
<link rel="stylesheet" href="https://fonts.googleapis.com/css2?family=Montserrat:wght@400;500;600;700&display=swap">
<style>
  :root {
    --blue: #3579bd;
    --blue-light: #4a8ccc;
    --grey: #3a3a3c;
    --grey-soft: #8f959c;
    --white: #ffffff;
    --backdrop: #e9e9ea;
  }
  * { box-sizing: border-box; margin: 0; padding: 0; }
  html, body { width: 1200px; height: 930px; overflow: hidden; }
  body {
    background: var(--backdrop);
    font-family: "Montserrat", sans-serif;
    position: relative;
  }
  .card {
    position: absolute;
    width: 700px;
    height: 400px;
    border-radius: 26px;
    overflow: hidden;
    box-shadow: 0 10px 28px rgba(0,0,0,0.18);
  }
  .card-back {
    left: 70px; top: 60px;
    background: linear-gradient(120deg, var(--blue-light), var(--blue) 55%);
    display: flex; align-items: center; justify-content: center;
  }
  .brand {
    display: flex; flex-direction: column; align-items: center;
    color: var(--white); font-weight: 700; text-transform: uppercase;
  }
  .brand-name { font-size: 44px; letter-spacing: 1px; line-height: 1; }
  .brand-sub {
    display: flex; align-items: center; gap: 12px;
    font-size: 19px; letter-spacing: 5px; margin-top: 8px;
  }
  .brand-sub::before, .brand-sub::after {
    content: ""; width: 56px; height: 2px; background: currentColor;
  }
  .card-front {
    left: 430px; top: 470px;
    background: var(--white);
  }
  .front-brand {
    position: absolute; left: 40px; top: 40px;
    color: var(--blue); align-items: flex-start;
  }
  .front-brand .brand-name { font-size: 30px; }
  .front-brand .brand-sub { font-size: 13px; letter-spacing: 4px; margin-top: 5px; color: var(--grey); }
  .front-brand .brand-sub::before, .front-brand .brand-sub::after { width: 36px; background: var(--grey); }
  .name-marker {
    position: absolute; left: 96px; top: 186px;
    width: 10px; height: 54px; background: var(--blue);
  }
  .name-block {
    position: absolute; left: 118px; top: 184px;
  }
  .agent-name {
    color: var(--blue); font-weight: 700; font-size: 26px; line-height: 32px;
    text-transform: uppercase; letter-spacing: 0.5px;
  }
  .agent-title { color: var(--grey); font-size: 17px; line-height: 22px; }
  .contact-band {
    position: absolute; left: 96px; top: 252px;
    width: 492px; height: 124px;
    background: var(--blue);
    color: var(--white);
    padding: 12px 0 0 26px;
    font-size: 16px; line-height: 25px;
  }
  .contact-row { display: flex; align-items: center; gap: 10px; white-space: nowrap; }
  .contact-row svg { width: 14px; height: 14px; flex: none; }
  .agent-photo {
    position: absolute; left: 598px; top: 150px;
    width: 78px; height: 226px;
    background: linear-gradient(180deg, #c9ced4, var(--grey-soft));
    border-left: 8px solid var(--grey);
  }
</style>
</head>
<body>
  <section class="card card-back">
    <div class="brand">
      <span class="brand-name">Maple Gable</span>
      <span class="brand-sub">Real Estate</span>
    </div>
  </section>

  <section class="card card-front">
    <div class="brand front-brand">
      <span class="brand-name">Maple Gable</span>
      <span class="brand-sub">Real Estate</span>
    </div>

    <div class="name-marker"></div>
    <div class="name-block">
      <p class="agent-name">Dana Whitfield</p>
      <p class="agent-title">Director</p>
    </div>

    <div class="agent-photo" role="img" aria-label="Agent portrait photo"></div>

    <div class="contact-band">
      <p class="contact-row">
        <svg viewBox="0 0 24 24" fill="currentColor"><path d="M6.6 10.8a15 15 0 0 0 6.6 6.6l2.2-2.2a1 1 0 0 1 1-.25 11.4 11.4 0 0 0 3.6.57 1 1 0 0 1 1 1V20a1 1 0 0 1-1 1A17 17 0 0 1 3 4a1 1 0 0 1 1-1h3.5a1 1 0 0 1 1 1c0 1.25.2 2.45.57 3.57a1 1 0 0 1-.25 1z"/></svg>
        (555) 214-3380
      </p>
      <p class="contact-row">
        <svg viewBox="0 0 24 24" fill="none" stroke="currentColor" stroke-width="2"><rect x="3" y="5" width="18" height="14" rx="1"/><path d="M3 6l9 7 9-7"/></svg>
        info@maplegable.com
      </p>
      <p class="contact-row">
        <svg viewBox="0 0 24 24" fill="none" stroke="currentColor" stroke-width="2"><circle cx="12" cy="12" r="9"/><path d="M3 12h18M12 3c3 3 3 15 0 18M12 3c-3 3-3 15 0 18"/></svg>
        www.maplegable.com
      </p>
      <p class="contact-row">
        <svg viewBox="0 0 24 24" fill="none" stroke="currentColor" stroke-width="2"><path d="M12 21s-7-6.2-7-11.5a7 7 0 0 1 14 0C19 14.8 12 21 12 21z"/><circle cx="12" cy="9.5" r="2.5"/></svg>
        48 Elm Row, Brookfield, ST 20418
      </p>
    </div>
  </section>
</body>
</html>
```